Acupuncture business needs business card design

I need a business card for an acupuncture clinic called "Harbourlight Wellness"
It will need the following details:
My name: Marcus Pelling
Acupuncturist
Member TVBH
KWF Treatment Provider
Ph numbers: 581 2734 027 418 5620
Email: marcus@hbwel.example.nz
On the back it will need a table with 2 columns for appointments, one column for time and one for date.

Industry/Entity Type

Clinic

Contact Information for Business Card

Marcus Pelling
Acupuncturist
Member TVBH
KWF Treatment Provider
Email: marcus@hbwel.example.nz

Requirements
Must have
• Marcus Pelling
• Acupuncturist
• Member TVBH
• KWF Treatment Provider
• Ph numbers: 581 2734 027 418 5620
• Email: marcus@hbwel.example.nz
• On the back it will need a table with 2 columns for appointments, one column for time and one for date.

```html
<!DOCTYPE html>
<html lang="en">
<head>
<meta charset="utf-8">
<title>Harbourlight Wellness – Business Card</title>
<link rel="stylesheet" href="https://fonts.googleapis.com/css2?family=Open+Sans:wght@400;600;700&display=swap">
<style>
  :root {
    --bg: #e9eaec;
    --card: #ffffff;
    --brand: #1a9fd0;
    --brand-band: #2ab4e3;
    --brand-deep: #0f7ea8;
    --ink: #3a3a3a;
    --muted: #8a8f94;
    --box-line: #6d6f72;
    --white: #ffffff;
  }
  * { box-sizing: border-box; margin: 0; padding: 0; }
  html, body { width: 1200px; height: 948px; overflow: hidden; }
  body {
    background: var(--bg);
    font-family: "Open Sans", Arial, sans-serif;
    color: var(--ink);
    position: relative;
  }
  .card {
    position: absolute;
    left: 250px;
    width: 700px;
    height: 400px;
    background: var(--card);
    box-shadow: 0 6px 18px rgba(0,0,0,0.12);
    overflow: hidden;
  }
  .card--front { top: 48px; }
  .card--back { top: 500px; }

  .brand {
    position: absolute;
    display: flex;
    align-items: center;
    gap: 14px;
  }
  .brand__dot {
    width: 40px; height: 40px;
    border-radius: 50%;
    background: var(--brand);
    flex: none;
  }
  .brand__name {
    font-weight: 600;
    font-size: 34px;
    letter-spacing: -0.3px;
    color: var(--brand);
    line-height: 1;
  }
  .brand__tagline {
    position: absolute;
    font-size: 11px;
    letter-spacing: 4.5px;
    text-transform: uppercase;
    color: var(--muted);
  }
  .card--front .brand { left: 46px; top: 52px; }
  .card--front .brand__tagline { left: 100px; top: 96px; }

  .front__band { position: absolute; left: 0; top: 0; width: 700px; height: 400px; }

  .contact {
    position: absolute;
    left: 380px;
    top: 218px;
    color: var(--white);
  }
  .contact__name { font-weight: 700; font-size: 20px; margin-bottom: 4px; }
  .contact__role { font-size: 14px; line-height: 1.45; }
  .contact__line {
    display: flex; align-items: center; gap: 10px;
    font-size: 14px; margin-top: 10px;
  }
  .contact__line svg { flex: none; }
  .contact__roles { margin-bottom: 6px; }

  .card--back .brand { left: 150px; top: 46px; }
  .card--back .brand__tagline { left: 204px; top: 90px; }

  .appointment {
    position: absolute;
    left: 70px;
    top: 150px;
    width: 560px;
  }
  .appointment__row {
    display: flex;
    align-items: flex-end;
    gap: 12px;
    height: 56px;
    margin-bottom: 20px;
  }
  .appointment__label {
    width: 56px;
    font-size: 17px;
    color: var(--ink);
    padding-bottom: 6px;
  }
  .appointment__box {
    height: 52px;
    border: 1.5px solid var(--box-line);
  }
  .appointment__box--wide { flex: 1; }
  .appointment__box--day { width: 190px; }
  .appointment__box--small { width: 70px; }
  .appointment__box--rest { flex: 1; }
  .website {
    position: absolute;
    left: 0; right: 0;
    top: 340px;
    text-align: center;
    font-size: 16px;
    letter-spacing: 4px;
    color: var(--ink);
  }
</style>
</head>
<body>

  <section class="card card--front" aria-label="Business card front">
    <svg class="front__band" viewBox="0 0 700 400" aria-hidden="true">
      <path d="M0 232 C 180 196, 430 168, 700 148 L700 400 L0 400 Z" fill="var(--brand-band)"/>
      <path d="M150 214 C 330 180, 520 150, 700 132 L700 142 C 520 160, 330 190, 150 214 Z" fill="var(--brand-deep)"/>
    </svg>

    <div class="brand">
      <span class="brand__dot"></span>
      <span class="brand__name">Harbourlight Wellness</span>
    </div>
    <div class="brand__tagline">Acupuncture Physiotherapy</div>

    <div class="contact">
      <div class="contact__name">Marcus Pelling</div>
      <div class="contact__roles">
        <div class="contact__role">Acupuncturist, Member TVBH</div>
        <div class="contact__role">KWF Treatment Provider</div>
      </div>
      <div class="contact__line">
        <svg width="16" height="16" viewBox="0 0 16 16" aria-hidden="true">
          <circle cx="8" cy="8" r="8" fill="var(--white)"/>
          <path d="M5.2 4.2 L6.6 4 L7.3 5.8 L6.5 6.5 C7 7.6 8 8.6 9.3 9.3 L10 8.6 L11.8 9.3 L11.6 10.8 C8 11 5 8 5.2 4.2 Z" fill="var(--brand-band)"/>
        </svg>
        <span>581 2734 · 027 418 5620</span>
      </div>
      <div class="contact__line">
        <svg width="16" height="16" viewBox="0 0 16 16" aria-hidden="true">
          <circle cx="8" cy="8" r="8" fill="var(--white)"/>
          <rect x="4" y="5" width="8" height="6" fill="none" stroke="var(--brand-band)" stroke-width="1.2"/>
          <path d="M4 5 L8 8.5 L12 5" fill="none" stroke="var(--brand-band)" stroke-width="1.2"/>
        </svg>
        <span>marcus@hbwel.example.nz</span>
      </div>
    </div>
  </section>

  <section class="card card--back" aria-label="Business card back">
    <div class="brand">
      <span class="brand__dot"></span>
      <span class="brand__name">Harbourlight Wellness</span>
    </div>
    <div class="brand__tagline">Acupuncture Physiotherapy</div>

    <div class="appointment">
      <div class="appointment__row">
        <span class="appointment__label">Time</span>
        <span class="appointment__box appointment__box--wide"></span>
      </div>
      <div class="appointment__row">
        <span class="appointment__label">Date</span>
        <span class="appointment__box appointment__box--day"></span>
        <span class="appointment__box appointment__box--small"></span>
        <span class="appointment__box appointment__box--rest"></span>
      </div>
    </div>

    <div class="website">www.hbwel.example.nz</div>
  </section>

</body>
</html>
```